Pelican HVAC WordPress website design

Design a new modern, clean, website for HVAC mechanical business that uses company logo/colors for branding and recognition. Files attached are just for band and color information. Here is a website design that appeals to me https://www.corvellsupply.example/

A clear description of who we are and what we do

An easily-navigated site map

An easily-navigated site map for mobile devices

Easy-to-find contact information

Obvious call to action for service, installs or to schedule estimates

about us page

Provide a way for potential customers to contact us via text or email

provide a way that allows a customer to upload a picture to request a service call or quote.
Updates

I'm looking for the design to be completed in WordPress

Industry/Entity Type

HVAC Mechanical & Building Automation / Controls contractor

Coding

Coded - Design and coding required

Number of Pages Required

5+ page

Colors
0054AA
0677BA
7BADD7
CADEEF
E8F1F8

Requirements
Must have
• Design a new modern, clean, website for HVAC mechanical business that uses company logo/colors for branding and recognition. Files attached are just for band and color information. Here is a website design that appeals to me https://www.corvellsupply.example/ A clear description of who we are and what we do An easily-navigated site map An easily-navigated site map for mobile devices Easy-to-find contact information Obvious call to action for service, installs or to schedule estimates about us page Provide a way for potential customers to contact us via text or email provide a way that allows a customer to upload a picture to request a service call or quote.
Nice to have

```html
<!DOCTYPE html>
<html lang="en">
<head>
<meta charset="utf-8">
<title>Pelican HVAC</title>
<link rel="stylesheet" href="https://fonts.googleapis.com/css2?family=Cinzel:wght@500;600&family=Roboto:wght@400;500;700&display=swap">
<style>
:root{
  --navy:#0b1f5e;
  --navy-deep:#0a2a6b;
  --blue:#0054AA;
  --blue-mid:#0677BA;
  --blue-soft:#7BADD7;
  --blue-pale:#CADEEF;
  --blue-mist:#E8F1F8;
  --ink:#1b1b1b;
  --grey-text:#777;
  --field:#efeef0;
  --page-grey:#f4f4f6;
  --star:#f47b20;
  --white:#fff;
  --black:#000;
}
*{box-sizing:border-box;margin:0;padding:0}
html,body{width:1200px;height:3764px;overflow:hidden}
body{position:relative;font-family:'Roboto',Arial,sans-serif;color:var(--ink);background:var(--white)}
.abs{position:absolute}
.serif{font-family:'Cinzel',Georgia,serif}
.btn{position:absolute;display:flex;align-items:center;justify-content:center;gap:8px;border-radius:24px;background:var(--navy);color:var(--white);font:700 15px 'Roboto',sans-serif;letter-spacing:.2px}
.btn .dot{width:14px;height:14px;border-radius:50%;background:var(--white);display:inline-flex;align-items:center;justify-content:center}
.btn .dot svg{width:8px;height:8px}
.brand{font:700 24px 'Roboto',sans-serif;color:var(--navy);display:flex;align-items:center;gap:8px;white-space:nowrap}
.brand .mark{width:22px;height:22px;border-radius:50%;background:var(--blue)}

/* header */
.topbar{top:0;left:0;width:1200px;height:44px;background:#f3f3f3}
.navrow{top:44px;left:0;width:1200px;height:57px;background:var(--white)}
.logo-plate{left:102px;top:12px;width:180px;height:108px;border-radius:50%;background:var(--white);display:flex;align-items:center;justify-content:center;z-index:3}
.top-cta{left:402px;top:13px;font:700 14px 'Roboto',sans-serif;color:var(--navy)}
.top-mail{left:640px;top:6px;display:flex;align-items:center;gap:12px;font-size:14px;color:var(--ink)}
.icon-circle{width:30px;height:30px;border-radius:50%;background:var(--navy);display:flex;align-items:center;justify-content:center}
.icon-circle svg{width:15px;height:15px}
.nav{left:390px;top:63px;display:flex;gap:40px;font:500 14px 'Roboto',sans-serif;color:var(--ink)}
.nav-mark{left:400px;top:93px;width:18px;height:18px;border:2px solid var(--navy);border-radius:50%;border-bottom-color:transparent;border-left-color:transparent;transform:rotate(-45deg)}
.call-panel{top:0;left:868px;width:332px;height:101px}
.call-text{left:977px;top:22px;color:var(--white)}
.call-text small{display:block;font-size:14px;margin-bottom:8px}
.call-text strong{font:500 21px 'Roboto',sans-serif}
.call-icon{left:917px;top:33px;width:38px;height:38px;border-radius:50%;background:var(--white);display:flex;align-items:center;justify-content:center}

/* hero */
.hero-photo{top:101px;left:0;width:1200px;height:780px;background:linear-gradient(100deg,#e4e1de 0%,#efedeb 45%,#f5f4f3 100%)}
.hero-figures{top:101px;left:20px;width:600px;height:720px;background:linear-gradient(180deg,#d7d2cd 0%,#c89070 40%,#3a4a78 75%,#2a3560 100%);opacity:.55;border-radius:4px}
.hero-welcome{left:655px;top:258px;font-size:19px;font-weight:500}
.hero-title{left:655px;top:318px;font-size:50px;font-weight:600;letter-spacing:.5px;color:var(--black)}
.hero-title span{color:var(--navy-deep)}
.hero-copy{left:655px;top:402px;width:420px;font-size:16.5px;line-height:30px;color:#222}
.hero-wave{top:540px;left:0;width:1200px;height:340px}

/* about */
.about-photo{left:110px;top:950px;width:460px;height:345px;border-radius:0 0 0 120px;background:linear-gradient(180deg,#fff 0%,#dfe4ee 25%,#4a5a8c 60%,#1e2b55 100%)}
.about-badge{left:155px;top:1200px;width:180px;height:92px;border-radius:50%;background:var(--white);display:flex;align-items:center;justify-content:center;box-shadow:0 0 0 3px var(--blue-pale)}
.heading{display:flex;align-items:flex-end;font-family:'Cinzel',Georgia,serif;font-weight:600;white-space:nowrap}
.heading.center{left:0;width:1200px;justify-content:center}
.heading b{font-weight:600;color:var(--navy-deep)}
.heading i{font-style:normal;color:var(--black);margin-left:12px}
.about-heading{left:660px;top:920px;font-size:38px;height:60px}
.about-copy{left:633px;top:1004px;width:450px;font-size:14.3px;line-height:25.8px;color:var(--grey-text);text-align:justify}
.about-copy p+p{margin-top:22px}

/* services */
.services{top:1400px;left:0;width:1200px;height:760px;background:linear-gradient(100deg,#0b2767 0%,#0a3a82 55%,#0a5b9f 100%)}
.services-heading{top:1493px;font-size:40px;height:64px}
.services-heading b,.services-heading i{color:var(--white)}
.service{top:1636px;width:200px;text-align:center;color:var(--white);font:700 18px 'Roboto',sans-serif}
.service svg{display:block;margin:0 auto 14px;width:100px;height:80px}
.divider{top:1628px;width:2px;height:150px;background:rgba(255,255,255,.7)}
.arrow{width:42px;height:42px;border-radius:50%;display:flex;align-items:center;justify-content:center}
.arrow svg{width:12px;height:12px}
.arrow.light{background:var(--white)}
.arrow.ring{border:1.5px solid var(--navy);background:var(--white)}
.arrow.solid{background:var(--navy)}
.services-btn{left:467px;top:1823px;width:266px;height:44px;background:var(--white);color:var(--ink);font-weight:500;font-size:15px}
.services-curve{top:1940px;left:0;width:1200px;height:220px}

/* testimonials */
.testi-heading{top:2064px;font-size:40px;height:64px}
.card{top:2188px;width:294px;height:216px;background:var(--white);border-radius:12px;box-shadow:0 2px 14px rgba(0,0,0,.12);padding:22px 24px}
.card .who{display:flex;gap:16px;align-items:flex-start}
.avatar{width:52px;height:52px;border-radius:50%;background:linear-gradient(180deg,#cdd6e6,#1f3f7a)}
.card .name{font:700 14px 'Roboto',sans-serif;margin-top:6px}
.card .stars{color:var(--star);font-size:14px;letter-spacing:2px;margin-top:8px}
.card p{margin-top:18px;font-size:14px;line-height:23px;color:var(--grey-text)}
.blog-bg{top:2420px;left:0;width:1200px;height:800px;background:var(--page-grey)}
.blog-curve{top:2420px;left:0;width:1200px;height:170px}

/* blog */
.blog-heading{top:2656px;font-size:40px;height:64px}
.post{width:285px;text-align:center}
.post-img{width:285px;height:226px}
.post-label{height:56px;background:var(--blue);color:var(--white);font:700 15px 'Roboto',sans-serif;display:flex;align-items:center;justify-content:center}
.post p{margin-top:20px;font:500 14.5px/22px 'Roboto',sans-serif;color:var(--ink)}

/* footer */
.footer-wave{top:3180px;left:0;width:1200px;height:584px}
.quote{left:115px;top:3158px;width:331px;height:459px;background:var(--white);border-radius:22px;overflow:hidden;box-shadow:0 2px 10px rgba(0,0,0,.15)}
.quote h2{height:84px;background:var(--navy);color:var(--white);font:700 22px 'Roboto',sans-serif;display:flex;align-items:center;justify-content:center;padding-left:20px}
.quote .fields{padding:24px 16px 0}
.field{height:44px;border-radius:22px;background:var(--field);font-size:13px;color:#555;padding:0 26px;display:flex;align-items:center;margin-bottom:8px}
.field.msg{height:92px;align-items:flex-start;padding-top:14px}
.submit{left:190px;top:3588px;width:171px;height:45px;font-size:15px}
.foot-logo{left:862px;top:3330px;width:180px;height:94px;border-radius:50%;background:var(--white);display:flex;align-items:center;justify-content:center}
.foot-logo .brand{font-size:21px}
.quick{left:604px;top:3478px;color:var(--white)}
.quick h3{font:500 17px 'Roboto',sans-serif;margin-bottom:18px}
.quick li{list-style:none;font-size:14.5px;margin-bottom:15px}
.contact{left:850px;top:3475px;color:var(--white);font-size:14px}
.contact .row{display:flex;align-items:center;gap:18px;margin-bottom:20px}
.contact .ic{width:36px;height:36px;border-radius:50%;background:var(--white);display:flex;align-items:center;justify-content:center;flex:none}
.contact .ic svg{width:17px;height:17px}
.contact .txt{line-height:26px}
.copyright{left:0;top:3684px;width:1200px;text-align:center;color:var(--white);font-size:13px}
.social{left:1028px;top:3686px;display:flex;gap:10px}
.social span{width:11px;height:11px;border-radius:50%;background:var(--white)}
</style>
</head>
<body>

<!-- header -->
<div class="abs topbar"></div>
<div class="abs navrow"></div>
<div class="abs logo-plate"><div class="brand"><span class="mark"></span>Pelican HVAC</div></div>
<div class="abs top-cta">SCHEDULE AN APPOINTMENT</div>
<div class="abs top-mail">
  <span class="icon-circle"><svg viewBox="0 0 20 20"><rect x="2" y="4" width="16" height="12" rx="2" fill="#fff"/><path d="M2.5 5 10 11l7.5-6" stroke="#0b1f5e" stroke-width="1.8" fill="none"/></svg></span>
  hello@pelicanhvac.example
</div>
<nav class="abs nav"><span>Home</span><span>About us</span><span>Services</span><span>Blog</span><span>Contact Us</span></nav>
<div class="abs nav-mark"></div>
<svg class="abs call-panel" viewBox="0 0 332 101"><path d="M0 0H332V101H40C28 70 16 30 0 0Z" fill="#0b1f5e"/></svg>
<div class="abs call-icon"><svg viewBox="0 0 24 24" width="16" height="16"><path d="M6.6 10.8a15 15 0 0 0 6.6 6.6l2.2-2.2a1 1 0 0 1 1-.25 11.4 11.4 0 0 0 3.6.57 1 1 0 0 1 1 1V20a1 1 0 0 1-1 1A17 17 0 0 1 3 4a1 1 0 0 1 1-1h3.5a1 1 0 0 1 1 1c0 1.250.2 2.45.57 3.57a1 1 0 0 1-.25 1z" fill="#0b1f5e"/></svg></div>
<div class="abs call-text"><small>Call Us Today at</small><strong>603-555-0148</strong></div>

<!-- hero -->
<div class="abs hero-photo" role="img" aria-label="Two HVAC technicians in orange shirts and navy overalls installing a wall-mounted air conditioner from a ladder"></div>
<div class="abs hero-figures" role="img" aria-label="Technicians working on a step ladder"></div>
<div class="abs hero-welcome">Welcome To</div>
<div class="abs hero-title serif"><span>PELICAN</span> HVAC</div>
<p class="abs hero-copy">Lorem ipsum dolor sit amet, consectetur adipiscing elit, sed do eiusmod tempor .</p>
<div class="btn" style="left:656px;top:504px;width:171px;height:44px">LEARN MORE <span class="dot"><svg viewBox="0 0 8 8"><path d="M2.5 1 5.5 4 2.5 7" stroke="#0b1f5e" stroke-width="1.6" fill="none"/></svg></span></div>
<div class="btn" style="left:843px;top:504px;width:189px;height:44px;justify-content:flex-start;padding-left:8px;gap:14px;font-size:16px;font-weight:500">
  <span style="width:32px;height:32px;border-radius:50%;background:#fff;display:flex;align-items:center;justify-content:center"><svg viewBox="0 0 24 24" width="15" height="15"><path d="M6.6 10.8a15 15 0 0 0 6.6 6.6l2.2-2.2a1 1 0 0 1 1-.25 11.4 11.4 0 0 0 3.6.57 1 1 0 0 1 1 1V20a1 1 0 0 1-1 1A17 17 0 0 1 3 4a1 1 0 0 1 1-1h3.5a1 1 0 0 1 1 1c0 1.25.2 2.45.57 3.57a1 1 0 0 1-.25 1z" fill="#0b1f5e"/></svg></span>603-555-0148</div>
<svg class="abs hero-wave" viewBox="0 0 1200 340" preserveAspectRatio="none">
  <defs><linearGradient id="heroBlue" x1="0" x2="1"><stop offset="0" stop-color="#0a2a6b"/><stop offset=".6" stop-color="#0b3c8a"/><stop offset="1" stop-color="#0054AA"/></linearGradient></defs>
  <path d="M0 200C260 330 650 300 1200 12V60C700 330 260 345 0 300Z" fill="url(#heroBlue)"/>
  <path d="M0 300C260 345 700 330 1200 60V340H0Z" fill="#fff"/>
</svg>

<!-- about -->
<div class="abs about-photo" role="img" aria-label="The service team in navy work uniforms standing together, manager holding a clipboard"></div>
<div class="abs about-badge"><div class="brand" style="font-size:20px">Pelican HVAC</div></div>
<h2 class="abs heading about-heading"><b>ABOUT</b><i>US</i></h2>
<div class="abs about-copy">
  <p>Sed ut perspiciatis unde omnis iste natus error sit voluptatem accusantium doloremque laudantium, totam rem aperiam, eaque ipsa quae ab illo inventore veritatis et quasi architecto beatae vitae dicta sunt explicabo. Nemo enim ipsam voluptatem quia voluptas sit aspernatur aut odit aut fugit, sed quia consequuntur magni dolores eos qui ratione voluptatem sequi nesciunt.</p>
  <p>Sed ut perspiciatis unde omnis iste natus error sit voluptatem accusantium doloremque laudantium, totam.</p>
</div>
<div class="btn" style="left:633px;top:1257px;width:171px;height:44px">LEARN MORE <span class="dot"><svg viewBox="0 0 8 8"><path d="M2.5 1 5.5 4 2.5 7" stroke="#0b1f5e" stroke-width="1.6" fill="none"/></svg></span></div>

<!-- services -->
<div class="abs services"></div>
<h2 class="abs heading center services-heading"><b>OUR</b><i>SERVICES</i></h2>
<div class="abs arrow light" style="left:39px;top:1685px"><svg viewBox="0 0 12 12"><path d="M8 2 4 6l4 4" stroke="#222" stroke-width="1.6" fill="none"/></svg></div>
<div class="abs arrow light" style="left:1119px;top:1685px"><svg viewBox="0 0 12 12"><path d="M4 2l4 4-4 4" stroke="#222" stroke-width="1.6" fill="none"/></svg></div>

<div class="abs service" style="left:84px">
  <svg viewBox="0 0 100 80"><circle cx="34" cy="40" r="26" fill="#0a2057"/><g stroke="#fff" stroke-width="2.2" fill="none"><rect x="30" y="14" width="56" height="28" rx="4"/><path d="M36 34h44"/><circle cx="46" cy="46" r="12" fill="#0a2a6b"/><path d="M46 38v16M39 42l14 8M53 42l-14 8"/><path d="M66 48c-3 4 3 6 0 10M74 48c-3 4 3 6 0 10M82 48c-3 4 3 6 0 10"/></g></svg>
  Air Conditioning</div>
<div class="abs divider" style="left:338px"></div>
<div class="abs service" style="left:362px">
  <svg viewBox="0 0 100 80"><circle cx="32" cy="40" r="26" fill="#0a2057"/><g stroke="#fff" stroke-width="2.4" fill="none"><rect x="30" y="28" width="52" height="40" rx="5"/><path d="M38 36v24M46 36v24M54 36v24M62 36v24M70 36v24"/><path d="M46 6c-4 5 4 8 0 14M56 6c-4 5 4 8 0 14M66 6c-4 5 4 8 0 14"/></g></svg>
  Heating</div>
<div class="abs divider" style="left:599px"></div>
<div class="abs service" style="left:640px">
  <svg viewBox="0 0 100 80"><circle cx="30" cy="40" r="26" fill="#0a2057"/><g stroke="#fff" stroke-width="2.4" fill="none"><circle cx="48" cy="32" r="18" stroke-dasharray="7 4"/><circle cx="48" cy="32" r="9"/><circle cx="72" cy="56" r="13" stroke-dasharray="5 3"/><circle cx="72" cy="56" r="5"/></g></svg>
  Maintenance</div>
<div class="abs divider" style="left:861px"></div>
<div class="abs service" style="left:917px">
  <svg viewBox="0 0 100 80"><circle cx="32" cy="40" r="26" fill="#0a2057"/><g stroke="#fff" stroke-width="2.4" fill="none"><circle cx="56" cy="38" r="28" stroke-dasharray="10 4"/><circle cx="56" cy="38" r="17"/><path d="M48 46l16-16"/><circle cx="50" cy="32" r="3"/><circle cx="62" cy="44" r="3"/></g></svg>
  Special Offers</div>

<div class="btn services-btn">SCHEDULE AN APPOINTMENT</div>
<svg class="abs services-curve" viewBox="0 0 1200 220" preserveAspectRatio="none">
  <path d="M0 210C320 40 760 -20 1200 60V220H0Z" fill="#fff"/>
  <path d="M760 10C950 10 1100 30 1200 60V20C1100 10 950 5 760 10Z" fill="#0a3d86"/>
</svg>

<!-- testimonials -->
<h2 class="abs heading center testi-heading"><b>OUR</b><i>TESTIMONIALS</i></h2>
<div class="abs blog-bg"></div>
<svg class="abs blog-curve" viewBox="0 0 1200 170" preserveAspectRatio="none"><path d="M0 0H1200V20C800 210 380 200 0 10Z" fill="#fff"/></svg>

<div class="abs arrow ring" style="left:39px;top:2281px"><svg viewBox="0 0 12 12"><path d="M8 2 4 6l4 4" stroke="#0b1f5e" stroke-width="1.6" fill="none"/></svg></div>
<div class="abs arrow solid" style="left:1119px;top:2281px"><svg viewBox="0 0 12 12"><path d="M4 2l4 4-4 4" stroke="#fff" stroke-width="1.6" fill="none"/></svg></div>

<div class="abs card" style="left:113px"><div class="who"><div class="avatar" role="img" aria-label="Customer portrait"></div><div><div class="name">JAN</div><div class="stars">★★★★★</div></div></div><p>Lorem ipsum dolor sit amet, sectetur adipiscing elit, sed do eiusmod mpor incididunt ut labore et dolore magna aliqua.Lorum Ipsum.</p></div>
<div class="abs card" style="left:451px"><div class="who"><div class="avatar" role="img" aria-label="Customer portrait"></div><div><div class="name">JAN</div><div class="stars">★★★★★</div></div></div><p>Lorem ipsum dolor sit amet, sectetur adipiscing elit, sed do eiusmod mpor incididunt ut labore et dolore magna aliqua.Lorum Ipsum.</p></div>
<div class="abs card" style="left:789px"><div class="who"><div class="avatar" role="img" aria-label="Customer portrait"></div><div><div class="name">JAN</div><div class="stars">★★★★★</div></div></div><p>Lorem ipsum dolor sit amet, sectetur adipiscing elit, sed do eiusmod mpor incididunt ut labore et dolore magna aliqua.Lorum Ipsum.</p></div>

<div class="btn" style="left:515px;top:2451px;width:170px;height:45px">LEARN MORE <span class="dot"><svg viewBox="0 0 8 8"><path d="M2.5 1 5.5 4 2.5 7" stroke="#0b1f5e" stroke-width="1.6" fill="none"/></svg></span></div>

<!-- blog -->
<h2 class="abs heading center blog-heading"><b>OUR</b><i>BLOG</i></h2>
<div class="abs arrow ring" style="left:39px;top:2864px"><svg viewBox="0 0 12 12"><path d="M8 2 4 6l4 4" stroke="#0b1f5e" stroke-width="1.6" fill="none"/></svg></div>
<div class="abs arrow solid" style="left:1119px;top:2864px"><svg viewBox="0 0 12 12"><path d="M4 2l4 4-4 4" stroke="#fff" stroke-width="1.6" fill="none"/></svg></div>

<article class="abs post" style="left:114px;top:2751px">
  <div class="post-img" role="img" aria-label="Technician shaking hands with a homeowner at the front door" style="background:linear-gradient(180deg,#b89c84,#6b5a4e 55%,#3a3f6a)"></div>
  <div class="post-label">LORUM IPSUM</div>
  <p>Sed ut perspiciatis unde omnis iste<br>natus error sit voluptatem accusantium</p>
</article>
<article class="abs post" style="left:458px;top:2794px">
  <div class="post-img" role="img" aria-label="Technician in a blue cap inspecting an outdoor condenser unit with a clipboard" style="background:linear-gradient(180deg,#e6e6e6,#9aa8c0 50%,#1e4fa0)"></div>
  <div class="post-label">LORUM IPSUM</div>
  <p>Sed ut perspiciatis unde omnis iste<br>natus error sit voluptatem accusantium</p>
</article>
<article class="abs post" style="left:801px;top:2751px">
  <div class="post-img" role="img" aria-label="Technician in a hard hat and hi-vis vest testing a rooftop unit" style="background:linear-gradient(180deg,#c9ccd0,#e0833a 50%,#6a6a6a)"></div>
  <div class="post-label">LORUM IPSUM</div>
  <p>Sed ut perspiciatis unde omnis iste<br>natus error sit voluptatem accusantium</p>
</article>

<!-- footer -->
<svg class="abs footer-wave" viewBox="0 0 1200 584" preserveAspectRatio="none">
  <defs><linearGradient id="footBlue" x1="0" x2="1"><stop offset="0" stop-color="#0a2a6b"/><stop offset="1" stop-color="#0054AA"/></linearGradient></defs>
  <path d="M0 230C300 190 520 80 1200 50V584H0Z" fill="#000"/>
  <path d="M430 120C700 30 950 10 1200 28V60C900 50 650 80 430 150Z" fill="url(#footBlue)"/>
  <path d="M0 380C60 340 110 310 150 300 100 340 50 380 0 410Z" fill="#0a3d86"/>
</svg>

<section class="abs quote">
  <h2>REQUEST A QUATE</h2>
  <div class="fields">
    <div class="field">NAME</div>
    <div class="field">EMAIL</div>
    <div class="field">PHONE</div>
    <div class="field">UPLOAD IMAGE</div>
    <div class="field msg">MESSAGE</div>
  </div>
</section>
<div class="btn submit">SUBMIT</div>

<div class="abs foot-logo"><div class="brand"><span class="mark"></span>Pelican HVAC</div></div>
<div class="abs quick">
  <h3>Quick Links</h3>
  <ul><li>Home</li><li>About</li><li>Services</li><li>Blog Contact</li></ul>
</div>
<div class="abs contact">
  <div class="row"><span class="ic"><svg viewBox="0 0 24 24"><path d="M12 2a7 7 0 0 0-7 7c0 5 7 13 7 13s7-8 7-13a7 7 0 0 0-7-7zm0 9.5A2.5 2.5 0 1 1 12 6.5a2.5 2.5 0 0 1 0 5z" fill="#0b1f5e"/></svg></span><span class="txt">Lorem ipsum dolor sit amet,<br>Lorem ipsum dolor .</span></div>
  <div class="row"><span class="ic"><svg viewBox="0 0 24 24"><path d="M6.6 10.8a15 15 0 0 0 6.6 6.6l2.2-2.2a1 1 0 0 1 1-.25 11.4 11.4 0 0 0 3.6.57 1 1 0 0 1 1 1V20a1 1 0 0 1-1 1A17 17 0 0 1 3 4a1 1 0 0 1 1-1h3.5a1 1 0 0 1 1 1c0 1.25.2 2.45.57 3.57a1 1 0 0 1-.25 1z" fill="#0b1f5e"/></svg></span><span class="txt">603-555-0148</span></div>
  <div class="row"><span class="ic"><svg viewBox="0 0 20 20"><rect x="2" y="4" width="16" height="12" rx="2" fill="#0b1f5e"/><path d="M2.5 5 10 11l7.5-6" stroke="#fff" stroke-width="1.6" fill="none"/></svg></span><span class="txt">hello@pelicanhvac.example</span></div>
</div>
<div class="abs copyright">Copyright@2024. All Rights Reserved By pelicanhvac</div>
<div class="abs social" aria-label="Social links"><span></span><span></span><span></span></div>

</body>
</html>
```